Dunmore Roofing

Want a professional looking business card

Industry/Entity Type

Business

Contact Information for Business Card

Paul Dunmore ( Owner) paul@dunmoreroofing-example.com, www.dunmoreroofing-example.com, Adress: 4172 Township road 43 Plantagenet,ON K9X4T2

```html
<!DOCTYPE html>
<html lang="en">
<head>
<meta charset="utf-8">
<title>Dunmore Roofing – Business Card</title>
<link href="https://fonts.googleapis.com/css2?family=Montserrat:wght@700;800&family=Open+Sans:wght@400;600&display=swap" rel="stylesheet">
<style>
  :root {
    --backdrop: #3a3532;
    --card: #161718;
    --card-edge: #0c0c0d;
    --brand-blue: #2f63b3;
    --silver: #9a9c9f;
    --grey-text: #8d8f92;
    --white-text: #f2f2f2;
    --divider: #6d6f72;
  }
  * { box-sizing: border-box; margin: 0; padding: 0; }
  html, body {
    width: 1200px; height: 864px; overflow: hidden;
    background: var(--backdrop);
  }
  .canvas { position: relative; width: 1200px; height: 864px; }
  .card {
    position: absolute;
    width: 600px; height: 343px;
    background: var(--card);
    border: 1px solid var(--card-edge);
    box-shadow: 0 14px 30px rgba(0,0,0,.45);
  }
  /* Front */
  .card-front { left: 60px; top: 70px; }
  .front-brand {
    position: absolute; left: 0; right: 0; top: 108px;
    text-align: center;
    font-family: "Montserrat", sans-serif; font-weight: 800;
    font-size: 46px; letter-spacing: 2px; line-height: 1.05;
    color: var(--silver); text-transform: uppercase;
  }
  .front-url {
    position: absolute; left: 0; right: 0; bottom: 40px;
    text-align: center;
    font-family: "Open Sans", sans-serif; font-size: 13px;
    letter-spacing: 5px; color: var(--grey-text);
  }
  /* Back */
  .card-back { left: 540px; top: 450px; }
  .back-brand {
    position: absolute; left: 24px; top: 118px; width: 262px;
    display: flex; align-items: center; gap: 10px;
  }
  .brand-square { width: 14px; height: 14px; background: var(--brand-blue); flex: none; }
  .brand-name {
    font-family: "Montserrat", sans-serif; font-weight: 800;
    font-size: 30px; line-height: 1.05; letter-spacing: 1px;
    color: var(--brand-blue); text-transform: uppercase;
  }
  .divider {
    position: absolute; left: 300px; top: 70px; width: 1px; height: 200px;
    background: linear-gradient(to bottom, transparent, var(--divider) 25%, var(--divider) 75%, transparent);
  }
  .contact {
    position: absolute; left: 318px; top: 84px; right: 12px;
    font-family: "Open Sans", sans-serif; color: var(--white-text);
  }
  .contact-name {
    font-weight: 600; font-size: 18px; color: var(--brand-blue);
    text-transform: uppercase; letter-spacing: .5px;
  }
  .contact-role { font-size: 13px; color: var(--grey-text); text-transform: uppercase; margin-bottom: 10px; }
  .contact-address { font-size: 13.5px; line-height: 1.4; margin-bottom: 8px; }
  .contact-line { display: flex; align-items: center; gap: 7px; font-size: 13px; line-height: 1.55; }
  .contact-line svg { width: 11px; height: 11px; flex: none; fill: var(--brand-blue); }
</style>
</head>
<body>
<div class="canvas">
  <section class="card card-front">
    <div class="front-brand">Dunmore<br>Roofing</div>
    <div class="front-url">www.dunmoreroofing-example.com</div>
  </section>

  <section class="card card-back">
    <div class="back-brand">
      <span class="brand-square"></span>
      <span class="brand-name">Dunmore<br>Roofing</span>
    </div>
    <div class="divider"></div>
    <div class="contact">
      <div class="contact-name">Paul Dunmore</div>
      <div class="contact-role">Owner</div>
      <div class="contact-address">4172 Township road 43<br>Hollowbrook, ON K9X4T2</div>
      <div class="contact-line">
        <svg viewBox="0 0 12 12" aria-hidden="true"><path d="M2.5 1l2 2-1 1.5c.7 1.5 1.8 2.6 3.3 3.3L8.3 6.8l2 2L9 10.8C5 10.3 1.7 7 1.2 3z"/></svg>
        <span>613 555 0147</span>
      </div>
      <div class="contact-line">
        <svg viewBox="0 0 12 12" aria-hidden="true"><path d="M1 2.5h10v7H1z M1.5 3l4.5 3.5L10.5 3" stroke="#161718" stroke-width=".9"/></svg>
        <span>paul@dunmoreroofing-example.com</span>
      </div>
      <div class="contact-line">
        <svg viewBox="0 0 12 12" aria-hidden="true"><circle cx="6" cy="6" r="5"/><path d="M1 6h10M6 1c2 2.7 2 7.3 0 10M6 1c-2 2.7-2 7.3 0 10" stroke="#161718" stroke-width=".8" fill="none"/></svg>
        <span>www.dunmoreroofing-example.com</span>
      </div>
    </div>
  </section>
</div>
</body>
</html>
```